Veterinary Pylon

My veterinary clinic is not clearly visible from the street and I want to place a Pylon next to my driveway. I want a modern, elegant straight Design, the Photo shows the sheduled place. One can see the clinic on our Homepage: www.tailbright-vethaus.at
The last pictures are examples for pylones I like

Target Market(s)

the passing cars often miss my entry...I want to show where to turn left

Colors
3276b5
33a6d7
00a990

Requirements
Must have
• High value, simple elegance, size: 250cm (high) x 100cm (width)
Nice to have
• Our Logo, arrow(?)

A special Text is not necessary but this will be an option:

Biegen sie hier ab und wir biegen es wieder hin!
Should not have
• Too much Color, the colors I have chosen are the possible colors but it‘s not necessary to use them.

```html
<!DOCTYPE html>
<html lang="de">
<head>
<meta charset="utf-8">
<title>Tailbright Vethaus – Pylon</title>
<link rel="stylesheet" href="https://fonts.googleapis.com/css2?family=Archivo+Black&display=swap">
<style>
  :root {
    --navy: #124b93;
    --deep-blue: #1560a0;
    --sky: #2fbcdf;
    --white: #ffffff;
  }
  html, body {
    margin: 0;
    padding: 0;
    width: 1200px;
    height: 3000px;
    overflow: hidden;
    background: var(--white);
  }
  .pylon {
    position: relative;
    width: 1200px;
    height: 3000px;
    background: var(--white);
    overflow: hidden;
  }
  .swoosh {
    position: absolute;
    left: 0;
    width: 1200px;
  }
  .swoosh--top { top: 0; height: 340px; }
  .swoosh--bottom { top: 2400px; height: 600px; }
  .brand-name {
    position: absolute;
    left: 0;
    top: 980px;
    width: 1200px;
    margin: 0;
    text-align: center;
    font-family: "Archivo Black", sans-serif;
    font-weight: 400;
    font-size: 112px;
    line-height: 1.15;
    letter-spacing: 2px;
    text-transform: uppercase;
    color: var(--navy);
  }
  .turn-arrow {
    position: absolute;
    left: 366px;
    top: 1595px;
    width: 484px;
    height: 484px;
  }
</style>
</head>
<body>
<main class="pylon">
  <svg class="swoosh swoosh--top" viewBox="0 0 1200 340" aria-hidden="true">
    <path d="M99 282 C500 350 890 250 1130 0 H1062 C810 250 460 325 99 282 Z" fill="var(--sky)"/>
    <path d="M0 0 H1026 C780 210 420 320 0 245 Z" fill="var(--navy)"/>
  </svg>

  <h1 class="brand-name">Tailbright<br>Vethaus</h1>

  <svg class="turn-arrow" viewBox="0 0 484 484" role="img" aria-label="Hier links abbiegen">
    <defs>
      <linearGradient id="arrowFill" x1="0" y1="0" x2="1" y2="0">
        <stop offset="0" stop-color="var(--navy)"/>
        <stop offset="1" stop-color="var(--sky)"/>
      </linearGradient>
    </defs>
    <circle cx="242" cy="242" r="242" fill="url(#arrowFill)"/>
    <polyline points="231,131 121,242 231,353" fill="none" stroke="var(--white)" stroke-width="23"/>
    <line x1="137" y1="242" x2="385" y2="242" stroke="var(--white)" stroke-width="23"/>
  </svg>

  <svg class="swoosh swoosh--bottom" viewBox="0 2400 1200 600" aria-hidden="true">
    <path d="M0 2563 C450 2420 950 2540 1200 2889 V2958 C950 2590 450 2478 0 2588 Z" fill="var(--sky)"/>
    <path d="M0 2604 C420 2500 900 2620 1194 3000 H0 Z" fill="var(--deep-blue)"/>
  </svg>
</main>
</body>
</html>
```